Real Estate Webpage Design

We have an existing website: ferndaleestatecollective.com.au
We focus customised service mainly on Property Management and second-hand property sales.
We are not entirely happy about the current design and layout can stay roughly the same as the back end coding is linked to a CRM system.
We would like to see the design are more reachable to our clients and appearing.
Please check our Website Design Draft for more details.

Industry/Entity Type

Real estate Agency

Number of Pages Required

5+ page

Font styles to use
Sans Serif

Colors

Designer to choose colors to be used in the design.

```html
<!DOCTYPE html>
<html lang="en">
<head>
<meta charset="utf-8">
<title>Ferndale Estate Collective</title>
<link rel="stylesheet" href="https://fonts.googleapis.com/css2?family=Baloo+2:wght@500;600;700&family=Mulish:ital,wght@0,400;0,600;0,700;1,400&display=swap">
<style>
:root{
  --gold:#e9b949;
  --gold-soft:#f3d27e;
  --navy:#2f3a4c;
  --ink:#1c1c1c;
  --text:#444;
  --muted:#9a9a9a;
  --line:#e6e6e6;
  --paper:#ffffff;
  --mist:#f2f2f2;
  --night:#0d0d0d;
}
*{box-sizing:border-box;margin:0;padding:0}
html,body{width:1200px;height:4285px;overflow:hidden}
body{position:relative;background:var(--paper);font-family:"Mulish",sans-serif;color:var(--text)}
.abs{position:absolute}
h1,h2,h3,.display{font-family:"Baloo 2",sans-serif;color:var(--ink);font-weight:600}

/* header */
.site-header{position:absolute;left:0;top:0;width:1200px;height:118px;background:var(--paper);box-shadow:0 2px 6px rgba(0,0,0,.06);z-index:3}
.brand{position:absolute;left:110px;top:28px;display:flex;align-items:center;gap:12px}
.brand-mark{width:52px;height:52px;border:5px solid var(--gold)}
.brand-name{font-family:"Baloo 2",sans-serif;font-weight:600;font-size:34px;line-height:1;color:var(--gold)}
.brand-sub{font-size:11px;color:var(--muted);letter-spacing:.5px;margin-top:2px}
.topbar{position:absolute;left:380px;top:0;width:710px;height:46px;background:var(--navy);clip-path:polygon(0 0,100% 0,96% 100%,3% 100%);color:#fff;font-size:13px;display:flex;align-items:center;gap:40px;padding-left:48px}
.topbar span{display:flex;align-items:center;gap:8px}
.nav{position:absolute;top:74px;left:0;font-size:14px;color:var(--text)}
.nav a{position:absolute;white-space:nowrap;text-decoration:none;color:inherit}
.nav a.active{color:var(--gold)}
.nav a.active::after{content:"";position:absolute;left:2px;top:36px;width:34px;height:5px;border-radius:3px;background:var(--gold)}

/* hero */
.hero{position:absolute;left:0;top:118px;width:1200px;height:740px;background:linear-gradient(180deg,#4a6e86 0%,#8fa9b5 30%,#5f7a4d 62%,#3d5a2a 100%)}
.hero-copy{position:absolute;left:110px;top:178px;width:430px}
.hero-copy h1{font-size:54px;line-height:1.15;color:#fff;font-weight:600}
.hero-copy p{font-size:13px;line-height:1.9;color:#f1f1f1;margin-top:10px}
.btn{display:inline-flex;align-items:center;justify-content:center;background:var(--gold);color:#fff;border-radius:30px;font-weight:700;font-size:14px;text-decoration:none}
.hero .btn{position:absolute;left:113px;top:375px;width:160px;height:52px}
.hero-edge{position:absolute;left:0;top:690px}

/* listings */
.section-title{position:absolute;left:0;width:1200px;text-align:center;font-size:32px}
.tabs{position:absolute;top:970px;left:0;width:1200px;display:flex;justify-content:center;gap:0;font-weight:700;font-size:16px;color:var(--ink)}
.tab{height:42px;display:flex;align-items:center;justify-content:center;border-radius:22px}
.tab.on{background:var(--gold);color:#fff}
.card{position:absolute;width:313px;height:418px;background:#fff;border-radius:12px;box-shadow:0 3px 14px rgba(0,0,0,.12);overflow:hidden}
.card .photo{height:225px}
.badge{position:absolute;right:20px;top:20px;background:var(--gold);color:#fff;font-size:11px;font-weight:700;border-radius:14px;padding:5px 12px}
.card .body{padding:20px 22px 0}
.price{font-family:"Baloo 2",sans-serif;font-weight:600;font-size:19px;color:var(--ink)}
.card h3{font-size:18px;margin-top:6px;font-weight:600}
.addr{display:flex;align-items:center;gap:8px;font-size:12px;color:var(--muted);margin-top:10px;padding-bottom:14px;border-bottom:1px solid var(--line)}
.stats{display:flex;gap:22px;font-size:13px;color:var(--text);margin-top:14px;padding-left:6px}
.stats span{display:flex;align-items:center;gap:6px}

/* welcome */
.welcome{position:absolute;left:0;top:2028px;width:1200px;height:468px;background:var(--navy)}
.welcome-art{position:absolute;left:110px;top:2008px;width:526px;height:508px;background:linear-gradient(135deg,var(--gold) 0%,#c99a2e 45%,#3a4658 46%,#cfcfcf 100%)}
.welcome-copy{position:absolute;left:695px;top:2068px;width:395px;color:#fff}
.welcome-copy h2{color:#fff;font-size:32px;line-height:1.35}
.welcome-copy p{font-size:14.5px;line-height:1.75;margin-top:18px;color:#eef0f3}
.welcome-copy .btn{margin-top:22px;width:160px;height:52px}

/* testimonials */
.quote-icon{position:absolute;left:573px;top:2594px;width:62px;height:62px;border-radius:50%;background:var(--gold);color:#fff;font-family:"Baloo 2",sans-serif;font-size:54px;line-height:86px;text-align:center;font-weight:700}
.lede{position:absolute;left:0;width:1200px;text-align:center;font-size:13.5px;line-height:1.85;color:var(--text)}
.t-card{position:absolute;top:2816px;width:407px;height:196px;background:#fff;box-shadow:0 2px 12px rgba(0,0,0,.09);padding:28px 26px;overflow:hidden}
.t-card.faded{opacity:.45}
.t-card p{font-style:italic;font-size:12.5px;line-height:2.05;color:#555}
.person{display:flex;align-items:center;gap:12px;margin-top:10px}
.avatar{width:52px;height:52px;border-radius:50%;background:linear-gradient(180deg,#cfd3d8,#7d8590)}
.person b{display:block;font-family:"Baloo 2",sans-serif;font-weight:500;font-size:18px;color:var(--ink);line-height:1.1}
.person small{font-size:14px;color:var(--muted)}
.dots{position:absolute;top:3074px;left:582px;display:flex;gap:6px}
.dots i{width:9px;height:9px;border-radius:50%;background:#bbb}
.dots i:first-child{background:var(--navy)}

/* contact */
.contact{position:absolute;left:0;top:3188px;width:1200px;height:700px;background:var(--mist)}
.field{position:absolute;height:50px;background:#fff;border:1px solid #ececec;display:flex;align-items:center;gap:8px;padding-left:20px;font-size:14px;color:#777}
.field.msg{align-items:flex-start;padding-top:16px}
.contact .btn{position:absolute;left:522px;top:3673px;width:160px;height:50px;font-size:14px}

/* footer */
.footer{position:absolute;left:0;top:3760px;width:1200px;height:525px}
.foot-brand{position:absolute;left:116px;top:3918px;width:280px;height:266px;background:#151515;display:flex;flex-direction:column;align-items:center;justify-content:center;gap:6px}
.foot-brand .brand-name{font-size:36px}
.foot-brand small{color:#fff;font-size:11px}
.foot-col{position:absolute;top:3968px;color:#fff;font-size:14.5px}
.foot-col h4{font-family:"Baloo 2",sans-serif;font-weight:500;font-size:22px;margin-bottom:12px}
.foot-col li{list-style:none;display:flex;gap:10px;line-height:1.6;margin-bottom:12px}
.foot-col.links li{margin-bottom:6px;font-size:14px}
.socials{display:flex;gap:8px}
.socials i{width:31px;height:31px;border-radius:50%;background:var(--gold);display:block}
.copyright{position:absolute;left:0;top:4218px;width:1200px;text-align:center;color:#fff;font-size:14px}
</style>
</head>
<body>

<header class="site-header">
  <div class="brand">
    <div class="brand-mark"></div>
    <div><div class="brand-name">Ferndale</div><div class="brand-sub">Estate Collective</div></div>
  </div>
  <div class="topbar">
    <span><svg width="11" height="14" viewBox="0 0 12 16"><path d="M6 0a6 6 0 0 0-6 6c0 4.5 6 10 6 10s6-5.5 6-10a6 6 0 0 0-6-6zm0 8.5A2.5 2.5 0 1 1 6 3.5a2.5 2.5 0 0 1 0 5z" fill="#fff"/></svg>118/4 Marlowe Street, Harrison, ACT, 2914</span>
    <span><svg width="13" height="13" viewBox="0 0 16 16"><path d="M3.6 1l2.3 3.2-1.4 1.7a9 9 0 0 0 5.6 5.6l1.7-1.4L15 12.4 13.6 15C6.8 15 1 9.2 1 2.4z" fill="#fff"/></svg>02 6188 3052</span>
    <span><i style="width:24px;height:24px;border-radius:50%;background:#c9d3e6;display:block"></i>En ▾</span>
  </div>
  <nav class="nav">
    <a class="active" style="left:420px">Home</a>
    <a style="left:503px">About Us</a>
    <a style="left:608px">Leasing</a>
    <a style="left:701px">Buy</a>
    <a style="left:769px">Sell</a>
    <a style="left:834px">Our Team</a>
    <a style="left:939px">Blog</a>
    <a style="left:1009px">Contact Us</a>
  </nav>
</header>

<section class="hero" role="img" aria-label="Photo of a blue weatherboard house on a green lawn at dusk">
  <div class="hero-copy">
    <h1>Ferndale, A Place To Call Home</h1>
    <p>Ferndale is built around “the home, the house”, buying a property is one of the most expensive expenses and important ...</p>
  </div>
  <a class="btn">Learn More</a>
  <svg class="hero-edge" width="1200" height="170" viewBox="0 0 1200 170">
    <polygon points="0,92 600,22 1080,160 1200,122 1200,170 0,170" fill="#e9b949"/>
    <polygon points="0,110 600,36 1200,118 1200,170 0,170" fill="#fff"/>
  </svg>
</section>

<h2 class="section-title" style="top:898px">This Month At Ferndale Estate Collective</h2>
<div class="tabs">
  <div class="tab on" style="width:112px">For Sale</div>
  <div class="tab" style="width:150px">For Lease</div>
  <div class="tab" style="width:132px">Open Times</div>
  <div class="tab" style="width:108px">Sold</div>
  <div class="tab" style="width:118px">Leased</div>
</div>

<article class="card" style="left:110px;top:1067px">
  <div class="photo" role="img" aria-label="Bright bathroom with dark vanity" style="background:linear-gradient(180deg,#f4f4f4,#3a3a3a 70%,#ddd)"></div>
  <span class="badge">Homes Available</span>
  <div class="body"><div class="price">$500,000+</div><h3>Gungahlin</h3>
    <div class="addr"><svg width="11" height="15" viewBox="0 0 12 16"><path d="M6 0a6 6 0 0 0-6 6c0 4.5 6 10 6 10s6-5.5 6-10a6 6 0 0 0-6-6z" fill="#e9b949"/></svg>Level 3/20 Marlowe Street..</div>
    <div class="stats"><span>⇄ 500 Sqft</span><span>▭ 3</span><span>▤ 4</span></div></div>
</article>
<article class="card" style="left:443px;top:1067px">
  <div class="photo" role="img" aria-label="Empty white room with timber floor" style="background:linear-gradient(180deg,#f6f6f6 55%,#8a6a4c)"></div>
  <div class="body"><div class="price">$369,900+</div><h3>Belconnen</h3>
    <div class="addr"><svg width="11" height="15" viewBox="0 0 12 16"><path d="M6 0a6 6 0 0 0-6 6c0 4.5 6 10 6 10s6-5.5 6-10a6 6 0 0 0-6-6z" fill="#e9b949"/></svg>88/12 Wattle Street Belconnen..</div>
    <div class="stats"><span>⇄ 500 Sqft</span><span>▭ 3</span><span>▤ 4</span></div></div>
</article>
<article class="card" style="left:775px;top:1067px">
  <div class="photo" role="img" aria-label="Red brick home with blossom trees" style="background:linear-gradient(180deg,#9ac2e6,#b06a6a 50%,#5d9a3a)"></div>
  <div class="body"><div class="price">$369,900+</div><h3>Lorem ipsum dolor sit amet</h3>
    <div class="addr"><svg width="11" height="15" viewBox="0 0 12 16"><path d="M6 0a6 6 0 0 0-6 6c0 4.5 6 10 6 10s6-5.5 6-10a6 6 0 0 0-6-6z" fill="#e9b949"/></svg>Lorem ipsum dolor sit amet</div>
    <div class="stats"><span>⇄ 500 Sqft</span><span>▭ 3</span><span>▤ 2</span></div></div>
</article>
<article class="card" style="left:110px;top:1507px">
  <div class="photo" role="img" aria-label="Large home lit at night" style="background:linear-gradient(180deg,#1f3358,#4a4a55 55%,#c89a4c)"></div>
  <div class="body"><div class="price">$369,900+</div><h3>Lorem ipsum dolor sit amet</h3>
    <div class="addr"><svg width="11" height="15" viewBox="0 0 12 16"><path d="M6 0a6 6 0 0 0-6 6c0 4.5 6 10 6 10s6-5.5 6-10a6 6 0 0 0-6-6z" fill="#e9b949"/></svg>Lorem ipsum dolor sit amet</div>
    <div class="stats"><span>⇄ 2508 Sqft</span><span>▭ 2</span><span>▤ 2</span></div></div>
</article>
<article class="card" style="left:443px;top:1507px">
  <div class="photo" role="img" aria-label="White cottage with garden" style="background:linear-gradient(180deg,#bcd6ef,#e8e8e4 50%,#5f8f3a)"></div>
  <span class="badge">Sold Out</span>
  <div class="body"><div class="price">$369,900+</div><h3>Lorem ipsum dolor sit amet</h3>
    <div class="addr"><svg width="11" height="15" viewBox="0 0 12 16"><path d="M6 0a6 6 0 0 0-6 6c0 4.5 6 10 6 10s6-5.5 6-10a6 6 0 0 0-6-6z" fill="#e9b949"/></svg>Lorem ipsum dolor sit amet</div>
    <div class="stats"><span>⇄ 2508 Sqft</span><span>▭ 2</span><span>▤ 2</span></div></div>
</article>
<article class="card" style="left:775px;top:1507px">
  <div class="photo" role="img" aria-label="Modern white two-storey house" style="background:linear-gradient(180deg,#a9c7e0,#ededed 50%,#6f9a46)"></div>
  <div class="body"><div class="price">$369,900+</div><h3>Lorem ipsum dolor sit amet</h3>
    <div class="addr"><svg width="11" height="15" viewBox="0 0 12 16"><path d="M6 0a6 6 0 0 0-6 6c0 4.5 6 10 6 10s6-5.5 6-10a6 6 0 0 0-6-6z" fill="#e9b949"/></svg>Lorem ipsum dolor sit amet</div>
    <div class="stats"><span>⇄ 2508 Sqft</span><span>▭ 2</span><span>▤ 2</span></div></div>
</article>

<section class="welcome"></section>
<div class="welcome-art" role="img" aria-label="Collage of warm-lit interior photos"></div>
<div class="welcome-copy">
  <h2>Welcome to Ferndale Estate Collective</h2>
  <p>Ferndale stands for “the home, the house”, buying a property is one of the most expensive expenses and important assets for people. Ferndale is a real estate company located in Gungahlin, Canberra.</p>
  <p>Being a portfolio sales agent and property manager, coupled with our high–profile international real estate experience</p>
  <a class="btn">Learn More</a>
</div>

<div class="quote-icon">“</div>
<h2 class="section-title" style="top:2668px">Testimonials</h2>
<p class="lede" style="top:2722px">Lorem ipsum dolor sit amet, consectetur adipiscing elit, sed do eiusmod tempor incididunt ut labore et<br>dolore magna aliqua. Quis ipsum suspendisse ultrices gravida.</p>

<div class="t-card faded" style="left:-247px"><p>Lorem ipsum dolor sit amet, consectetur adipiscing elit, sed do eiusmod tempor incididunt ut labore et dolore magna</p></div>
<div class="t-card" style="left:183px"><p>Hannah is my best property manager! Always happy to response my queries and keep us well informed at all stage. I will definitely recommend her to my friends.</p>
  <div class="person"><div class="avatar"></div><div><b>Mei Lin</b><small>Lorem Ipsum</small></div></div></div>
<div class="t-card" style="left:611px"><p>Very good service. Our property manager is very responsible, prompting and cares about detail. They use the system to track everything so no need to worry about miscommuni-</p>
  <div class="person"><div class="avatar"></div><div><b>Tara Chen</b><small>Lorem Ipsum</small></div></div></div>
<div class="t-card faded" style="left:1040px"><p>Very good service. Our property manager is very responsible, prompting and cares about detail.</p>
  <div class="person"><div class="avatar"></div><div><b>Tara Chen</b><small>Lorem Ipsum</small></div></div></div>
<div class="dots"><i></i><i></i><i></i></div>

<section class="contact"></section>
<h2 class="section-title" style="top:3252px">Contact Us</h2>
<p class="lede" style="top:3308px">Lorem ipsum dolor sit amet, consectetur adipiscing elit, sed do eiusmod tempor<br>incididunt ut labore et dolore magna aliqua.</p>
<div class="field" style="left:110px;top:3380px;width:316px">👤︎ Name</div>
<div class="field" style="left:442px;top:3380px;width:316px">✉︎ Email</div>
<div class="field" style="left:773px;top:3380px;width:316px">☏ Phone</div>
<div class="field msg" style="left:110px;top:3449px;width:979px;height:171px">▭ Message</div>
<a class="btn" style="position:absolute;left:522px;top:3673px;width:160px;height:50px">Send Message</a>

<footer class="footer">
  <svg width="1200" height="525" viewBox="0 0 1200 525" style="position:absolute;left:0;top:0">
    <polygon points="0,68 108,12 600,168 1083,4 1200,58 1200,525 0,525" fill="#e9b949"/>
    <polygon points="0,84 108,30 600,180 1083,22 1200,74 1200,525 0,525" fill="#0d0d0d"/>
  </svg>
</footer>
<div class="foot-brand">
  <div style="width:62px;height:62px;border:6px solid var(--gold)"></div>
  <div class="brand-name">Ferndale</div>
  <small>Estate Collective</small>
</div>
<div class="foot-col" style="left:404px;width:250px">
  <h4>Contact Us</h4>
  <ul>
    <li><span>⌖</span>118/4 Marlowe Street, Harrison, ACT, 2914</li>
    <li><span>☏</span>02 6188 3052</li>
    <li><span>✉</span>info@ferndaleestatecollective.com.au</li>
  </ul>
</div>
<div class="foot-col links" style="left:687px">
  <h4>Support</h4>
  <ul><li>Terms &amp; Conditions</li><li>Contact us</li><li>Privacy Policy</li></ul>
</div>
<div class="foot-col" style="left:895px">
  <h4>Follow Us</h4>
  <div class="socials"><i></i><i></i><i></i><i></i></div>
</div>
<div class="copyright">©Copyrights 2022 Ferndale Estate Collective &nbsp;|&nbsp;&nbsp; All Rights Reserved</div>

</body>
</html>
```